Vantrel System Web Page Design

This project is to design 6 pages of a web based medical system for clinics, hospitals, drugs suppliers, general items suppliers, insurance company, laboratories and patients (basically all parties which could be involved in).We want the designs of the browser, button, icon and layout are based on Zeltor, which is user friendly, looks professional, simple and neat but with powerful functions. We have uploaded few pictures of another system, please do not copy its design because this is not what we are looking for, the pictures are for you to know the elements should be included in our pages. Vantrel web-base system, design 6 pages1. Login PageShould include the following elements-company id with input field-login id with input field-password with input field2. Main Page (Navigation page)Should include the following elements-Appointment-Consultation-Patient-Drugs inventory -General supplies inventory -Laboratory-Suppliers-Insurance-Reports 3. Appointment PageShould include all the the elements in the respective pictures plus the followings-Daily View, Weekly View, Monthly View buttons4. Consultation PageShould include all the the elements in the respective picture5. Patient Page5.1 General information Should include all the the elements in the respective picture5.2 medical history/lab reportsShould include all the the elements in the respective picture plus the followings-Notify patient button-Share report button.
Updated on 28 Nov:
Please stop using Harbor Suite in your designs which is not the name of our system. We have just rename our system to Vantrel, please take note.
We need the system to look professional not playful, do not use too many colors and playful icons.

```html
<!DOCTYPE html>
<html lang="en">
<head>
<meta charset="utf-8">
<title>Vantrel – Main Navigation</title>
<link href="https://fonts.googleapis.com/css2?family=Open+Sans:wght@400;600&display=swap" rel="stylesheet">
<style>
:root{
  --navy:#1d3557;
  --text-dark:#3a4452;
  --white:#ffffff;
  --tile:rgba(38,168,181,0.82);
  --side-1:#1f8fa2;
  --side-2:#14a5b4;
  --side-3:#0fb6c4;
  --side-4:#0dc3cf;
  --side-5:#0bd0da;
  --side-6:#0ae0e8;
  --hero-a:#8fc0e4;
  --hero-b:#a9d1ee;
  --hero-c:#7fb3dc;
}
*{box-sizing:border-box;margin:0;padding:0}
html,body{width:1200px;height:674px;overflow:hidden}
body{position:relative;font-family:'Open Sans',sans-serif;background:var(--hero-b)}
.hero-photo{position:absolute;left:0;top:45px;width:1200px;height:629px;
  background:radial-gradient(ellipse at 50% 40%,var(--hero-b) 0%,var(--hero-a) 55%,var(--hero-c) 100%)}
.topbar{position:absolute;left:0;top:0;width:1200px;height:45px;background:var(--white);
  font-size:11.5px;color:var(--text-dark)}
.topbar .info{position:absolute;top:11px;display:flex;align-items:center;gap:7px;height:22px}
.topbar .dot{width:22px;height:22px;border-radius:50%;background:var(--navy);display:flex;align-items:center;justify-content:center}
.avatar{width:22px;height:22px;border-radius:50%;background:#8a8f96}
.lang-mark{width:18px;height:12px;background:#24406e}
.chev{width:8px;height:5px}
.brand{position:absolute;left:0;width:1200px;top:78px;display:flex;justify-content:center;align-items:center;gap:10px}
.brand .mark{width:16px;height:16px;border-radius:50%;background:#1cb0b5}
.brand .name{font-size:30px;font-weight:400;color:var(--white);letter-spacing:2px}
.tile{position:absolute;width:135px;height:124px;background:var(--tile);border-radius:5px;color:var(--white);text-align:center}
.tile svg{position:absolute;left:50%;top:24px;transform:translateX(-50%);width:36px;height:36px}
.tile .label{position:absolute;left:0;width:100%;top:75px;font-size:13px;line-height:18px}
.side{position:absolute;left:1126px;top:140px;width:74px}
.side .item{height:73.6px;color:var(--white);text-align:center;font-size:9.5px;line-height:13px;
  display:flex;flex-direction:column;align-items:center;justify-content:flex-end;padding-bottom:8px}
.side .item svg{width:28px;height:28px;margin-bottom:6px}
.footer{position:absolute;left:0;top:620px;width:1200px;text-align:center;font-size:12.5px;color:var(--text-dark)}
</style>
</head>
<body>
<div class="hero-photo" role="img" aria-label="Background photograph of a doctor with a child and mother in a bright clinic, tinted light blue"></div>

<header class="topbar">
  <div class="info" style="left:173px">
    <span class="dot"><svg width="11" height="11" viewBox="0 0 24 24"><path fill="#fff" d="M6.6 10.8a15 15 0 0 0 6.6 6.6l2.2-2.2c.3-.3.7-.4 1-.2 1.1.4 2.3.6 3.6.6.6 0 1 .4 1 1V20c0 .6-.4 1-1 1A17 17 0 0 1 3 4c0-.6.4-1 1-1h3.5c.6 0 1 .4 1 1 0 1.3.2 2.5.6 3.6.1.3 0 .7-.2 1z"/></svg></span>
    <span>000-0000-0000</span>
  </div>
  <div class="info" style="left:308px">
    <span class="dot"><svg width="11" height="11" viewBox="0 0 24 24"><path fill="#fff" d="M12 2a7 7 0 0 0-7 7c0 5 7 13 7 13s7-8 7-13a7 7 0 0 0-7-7zm0 9.5A2.5 2.5 0 1 1 12 6.5a2.5 2.5 0 0 1 0 5z"/></svg></span>
    <span>25A, Nemo enim ipsam voluptatem</span>
  </div>
  <div class="info" style="left:550px">
    <span class="dot"><svg width="12" height="12" viewBox="0 0 24 24"><circle cx="12" cy="12" r="8" fill="none" stroke="#fff" stroke-width="2.5"/><path d="M12 7v5h4" fill="none" stroke="#fff" stroke-width="2.5"/></svg></span>
    <span>Mon - Sat: 8:00A.M. - 7:00P.M.</span>
  </div>
  <div class="info" style="left:845px">
    <span class="avatar" role="img" aria-label="User profile photo"></span>
    <span>Tomas Hale</span>
    <svg class="chev" viewBox="0 0 8 5"><path d="M1 1l3 3 3-3" fill="none" stroke="#555" stroke-width="1.2"/></svg>
  </div>
  <div class="info" style="left:988px">
    <span class="lang-mark" role="img" aria-label="Language: English"></span>
    <svg class="chev" viewBox="0 0 8 5"><path d="M1 1l3 3 3-3" fill="none" stroke="#555" stroke-width="1.2"/></svg>
  </div>
</header>

<div class="brand"><span class="mark"></span><span class="name">Vantrel</span></div>

<main>
  <a class="tile" style="left:307px;top:306px">
    <svg viewBox="0 0 36 36" fill="none" stroke="#fff" stroke-width="2.4"><rect x="4" y="7" width="28" height="25" rx="2"/><path d="M4 13h28M11 3v7M25 3v7"/><path fill="#fff" stroke="none" d="M9 17h4v3H9zM16 17h4v3h-4zM23 17h4v3h-4zM9 23h4v3H9zM16 23h4v3h-4z"/></svg>
    <span class="label">Appointment</span>
  </a>
  <a class="tile" style="left:458px;top:306px">
    <svg viewBox="0 0 36 36"><circle cx="18" cy="16" r="11" fill="#fff"/><path d="M6 17a12 12 0 0 1 24 0" fill="none" stroke="#fff" stroke-width="2.5"/><rect x="4" y="15" width="5" height="8" rx="2" fill="#fff"/><rect x="27" y="15" width="5" height="8" rx="2" fill="#fff"/><path d="M29 23c0 5-4 8-9 8" fill="none" stroke="#fff" stroke-width="2"/><path d="M10 13c4 2 12 2 16 0v6H10z" fill="#26a8b5"/></svg>
    <span class="label">Consultation</span>
  </a>
  <a class="tile" style="left:608px;top:306px">
    <svg viewBox="0 0 36 36" fill="#fff"><rect x="3" y="14" width="3" height="18"/><rect x="6" y="24" width="27" height="4"/><rect x="30" y="24" width="3" height="8"/><circle cx="11" cy="20" r="3"/><rect x="16" y="18" width="17" height="6" rx="2"/><path d="M22 3h2v4h4v2h-4v4h-2V9h-4V7h4z"/></svg>
    <span class="label">Patient</span>
  </a>
  <a class="tile" style="left:758px;top:306px">
    <svg viewBox="0 0 36 36" fill="#fff"><rect x="4" y="10" width="22" height="12" rx="6" transform="rotate(-45 15 16)"/><circle cx="24" cy="24" r="9"/><path d="M24 16v16" stroke="#26a8b5" stroke-width="2"/></svg>
    <span class="label">Drugs Inventory</span>
  </a>
  <a class="tile" style="left:307px;top:446px">
    <svg viewBox="0 0 36 36" fill="#fff"><rect x="4" y="12" width="28" height="20" rx="3"/><rect x="8" y="8" width="20" height="5" rx="1"/><rect x="13" y="18" width="10" height="4" fill="#26a8b5"/><path d="M18 1v4M10 3l2 3M26 3l-2 3" stroke="#fff" stroke-width="2"/></svg>
    <span class="label">General Suppliers<br>Inventory</span>
  </a>
  <a class="tile" style="left:458px;top:446px">
    <svg viewBox="0 0 36 36" fill="#fff"><rect x="14" y="3" width="6" height="16" rx="1" transform="rotate(-20 17 11)"/><rect x="10" y="22" width="16" height="3"/><path d="M8 31h22v3H8z"/><path d="M22 14a8 8 0 0 1-4 13" fill="none" stroke="#fff" stroke-width="3"/></svg>
    <span class="label">Laboratory</span>
  </a>
  <a class="tile" style="left:608px;top:446px">
    <svg viewBox="0 0 36 36" fill="#fff"><circle cx="9" cy="5" r="3.5"/><path d="M5 10h7l3 9h-4v13H7V22H4z"/><rect x="17" y="14" width="10" height="8"/><rect x="17" y="23" width="15" height="6"/><circle cx="20" cy="32" r="2"/><circle cx="29" cy="32" r="2"/></svg>
    <span class="label">Suppliers</span>
  </a>
  <a class="tile" style="left:758px;top:446px">
    <svg viewBox="0 0 36 36" fill="#fff"><path d="M18 22S9 15 9 10a4.5 4.5 0 0 1 9-1 4.5 4.5 0 0 1 9 1c0 5-9 12-9 12z"/><path d="M3 14c2 7 6 12 12 15v5H11v-3C6 27 3 21 3 14zM33 14c-2 7-6 12-12 15v5h4v-3c5-4 8-10 8-17z"/></svg>
    <span class="label">Insurance</span>
  </a>
</main>

<nav class="side">
  <div class="item" style="background:var(--side-1)">
    <svg viewBox="0 0 28 28" fill="none" stroke="#fff" stroke-width="1.6"><rect x="5" y="2" width="18" height="24" rx="1"/><rect x="8" y="6" width="12" height="8"/><path d="M8 18h12M8 21h12"/></svg>REPORTS</div>
  <div class="item" style="background:var(--side-2)">
    <svg viewBox="0 0 28 28" fill="none" stroke="#fff" stroke-width="1.6"><path d="M5 2h13l5 5v19H5z"/><path d="M14 9v10M9 14h10"/></svg>REQUEST<br>FORM</div>
  <div class="item" style="background:var(--side-3)">
    <svg viewBox="0 0 28 28" fill="none" stroke="#fff" stroke-width="1.6"><rect x="3" y="5" width="22" height="20" rx="1"/><path d="M3 10h22M8 2v5M20 2v5M7 14h2M12 14h2M17 14h2M7 18h2M12 18h2M17 18h2M7 22h2M12 22h2"/></svg>DOCTORS<br>TIMETABLE</div>
  <div class="item" style="background:var(--side-4)">
    <svg viewBox="0 0 28 28" fill="none" stroke="#fff" stroke-width="1.6"><rect x="5" y="1" width="18" height="26" rx="1"/><rect x="8" y="4" width="12" height="5"/><path d="M8 12h3v3H8zM12.5 12h3v3h-3zM17 12h3v3h-3zM8 17h3v3H8zM12.5 17h3v3h-3zM17 17h3v8h-3zM8 22h3v3H8zM12.5 22h3v3h-3z"/></svg>CALCULATOR</div>
  <div class="item" style="background:var(--side-5)">
    <svg viewBox="0 0 28 28" fill="none" stroke="#fff" stroke-width="1.6"><path d="M7 4l4 5-2 3a13 13 0 0 0 7 7l3-2 5 4-3 4C12 25 3 16 3 7z"/><path d="M16 4a8 8 0 0 1 8 8M16 8a4 4 0 0 1 4 4"/></svg>EMERGENCY<br>CASE</div>
  <div class="item" style="background:var(--side-6)">
    <svg viewBox="0 0 28 28" fill="none" stroke="#fff" stroke-width="1.6"><path d="M14 26S6 17 6 11a8 8 0 0 1 16 0c0 6-8 15-8 15z"/><circle cx="14" cy="11" r="3"/></svg>LOCATION</div>
</nav>

<footer class="footer">© Copyright information here</footer>
</body>
</html>
```